A private security company called "Tavron Security Services Ltd"

Hello everybody,

We need a web page for a company based in NZ. It is mainly an informative website so it would be wonderful if the designer puts their absolute best into making it a website that I would really appreciate. The website needs to show professionalism and also needs to make our web surfers find the information they need in a click. the company's colour is black and silver, and if those two colours could be integrated into the website it would be absolutely lovely. Please do contact me for any information.

Sincerely,
Dorian Vaskel

Industry/Entity Type

Security

```html
<!DOCTYPE html>
<html lang="en">
<head>
<meta charset="utf-8">
<title>Tavron Security Services Ltd</title>
<link href="https://fonts.googleapis.com/css2?family=Roboto+Condensed:wght@400;700&family=Arimo:wght@400;700&display=swap" rel="stylesheet">
<style>
:root{
  --ink:#1c1c1c;
  --text:#555;
  --muted:#8a8a8a;
  --line:#d6d6d6;
  --white:#fff;
  --hero-top:#6a6a6a;
  --hero-bottom:#2b2b2b;
  --footer:#3a3a3a;
  --footer-dark:#2a2a2a;
  --footer-text:#9a9a9a;
  --field:#6a6a6a;
}
*{margin:0;padding:0;box-sizing:border-box}
html,body{width:1200px;height:2748px;overflow:hidden}
body{position:relative;background:var(--white);font-family:"Arimo",Arial,sans-serif;color:var(--text)}

/* header */
.site-header{position:absolute;left:0;top:0;width:1200px;height:157px;background:linear-gradient(#ffffff,#e4e4e4);border-bottom:1px solid #c9c9c9}
.brand{position:absolute;left:157px;top:68px;display:flex;align-items:center;gap:12px;font-family:"Roboto Condensed",sans-serif;font-weight:700;font-size:25px;color:var(--ink);line-height:1}
.brand-mark{width:22px;height:22px;background:var(--ink);border-radius:50%}
.brand small{display:block;font-size:13px;font-weight:700;letter-spacing:.5px;margin-top:3px}
.main-nav{position:absolute;top:100px;left:416px;width:627px;display:flex;justify-content:space-between;font-family:"Roboto Condensed",sans-serif;font-size:14px;color:var(--ink)}
.social{position:absolute;display:flex;gap:11px}
.social span{width:30px;height:30px;border-radius:50%;background:#b5b5b5;display:block}
.header-social{left:933px;top:32px}

/* hero */
.hero{position:absolute;left:0;top:157px;width:1200px;height:517px;background:radial-gradient(ellipse at 55% 30%,var(--hero-top),var(--hero-bottom) 75%)}
.hero-title{position:absolute;left:216px;top:228px;font-family:"Roboto Condensed",sans-serif;font-weight:400;font-size:31px;line-height:44px;color:#f2f2f2;white-space:nowrap}
.hero-title b{font-weight:400;font-size:38px}
.hero-photo{position:absolute;left:720px;top:60px;width:220px;height:457px;background:linear-gradient(90deg,#5c5c5c,#d9d9d9 45%,#8e8e8e);border-radius:6px 6px 0 0;opacity:.85}
.arrow{position:absolute;width:50px;height:50px;border-radius:50%;background:rgba(120,120,120,.8);display:flex;align-items:center;justify-content:center}
.arrow.small{width:34px;height:34px;background:#bbb}

/* solutions */
.solutions{position:absolute;left:0;top:674px;width:1200px;height:711px;background:linear-gradient(#f4f4f4,#e0e0e0)}
.section-title{position:absolute;width:1200px;text-align:center;font-family:"Roboto Condensed",sans-serif;font-weight:400;font-size:37px;color:var(--ink)}
.services-list{position:absolute;left:157px;top:150px;width:210px}
.services-list h3{font-family:"Roboto Condensed",sans-serif;font-weight:400;font-size:22px;color:var(--ink);margin-bottom:20px}
.services-list li{list-style:none;font-size:12.5px;color:var(--muted);margin-bottom:20px;padding-left:30px;position:relative;line-height:16px}
.services-list li::before{content:"›";position:absolute;left:0;top:0;width:16px;height:16px;border-radius:50%;background:#ddd;color:#888;font-size:13px;text-align:center;line-height:15px}
.promo{position:absolute;left:157px;top:422px;width:212px;height:253px;background:linear-gradient(#8a8a8a,#d8d8d8 70%,#bdbdbd);border:1px solid #aaa;padding:18px 16px}
.promo p{font-family:"Roboto Condensed",sans-serif;font-size:18px;color:#f0f0f0;line-height:25px}
.promo .phone{font-size:23px;margin-top:2px}
.promo .promo-brand{position:absolute;left:16px;bottom:24px;display:flex;align-items:center;gap:8px;font-family:"Roboto Condensed",sans-serif;font-weight:700;font-size:22px;color:var(--ink)}
.promo .promo-brand i{width:18px;height:18px;border-radius:50%;background:var(--ink);display:block}
.card{position:absolute;border-left:1px solid var(--line);border-right:1px solid var(--line);border-bottom:1px solid var(--line);padding:0 14px}
.card h4{display:flex;align-items:center;gap:8px;font-family:"Roboto Condensed",sans-serif;font-weight:400;font-size:15.5px;letter-spacing:-.2px;white-space:nowrap;color:var(--ink);height:44px;margin-bottom:18px}
.card h4 svg{flex:none}
.card p{font-size:11px;line-height:15px;color:var(--muted);margin-bottom:12px}
.btn{position:absolute;right:14px;background:linear-gradient(#fff,#e2e2e2);border:1px solid #c4c4c4;border-radius:3px;font-size:11px;color:#333;padding:6px 10px}

/* industries */
.industries{position:absolute;left:0;top:1385px;width:1200px;height:402px;background:var(--white)}
.industry{position:absolute;top:147px;width:198px;text-align:center}
.industry .ph{width:198px;height:156px;border:4px solid #e6e6e6;box-shadow:0 1px 3px rgba(0,0,0,.2)}
.industry h5{font-family:"Roboto Condensed",sans-serif;font-weight:400;font-size:18px;color:var(--ink);margin-top:12px}

/* solutions split */
.split{position:absolute;left:0;top:1787px;width:1200px;height:481px;background:linear-gradient(#f3f3f3,#e8e8e8)}
.split-divider{position:absolute;left:600px;top:60px;width:2px;height:380px;background:linear-gradient(transparent,#cfcfcf,transparent)}
.solution{position:absolute;top:0;width:380px;text-align:center}
.solution .ph{width:176px;height:176px;border-radius:50%;border:8px solid #e0e0e0;margin:78px auto 0;box-shadow:0 2px 6px rgba(0,0,0,.15)}
.solution h5{font-family:"Roboto Condensed",sans-serif;font-weight:400;font-size:18px;color:var(--ink);margin-top:22px}
.solution p{font-size:12px;line-height:15px;color:#aaa;margin:8px 10px 0}
.solution .btn{position:static;display:inline-block;margin-top:20px;padding:8px 22px;font-size:12px}

/* footer */
.site-footer{position:absolute;left:0;top:2268px;width:1200px;height:480px;background:linear-gradient(#4a4a4a,var(--footer) 40%,var(--footer-dark))}
.site-footer h3{position:absolute;top:60px;font-family:"Roboto Condensed",sans-serif;font-weight:400;font-size:26px;color:#eee}
.footer-about{position:absolute;left:157px;top:130px;width:310px;font-size:12px;line-height:14px;color:var(--footer-text)}
.footer-about p{margin-bottom:14px}
.quick-links{position:absolute;left:540px;top:128px}
.quick-links li{list-style:none;font-size:11px;color:var(--footer-text);margin-bottom:17px;padding-left:20px;position:relative}
.quick-links li::before{content:"›";position:absolute;left:0;top:-3px;color:#ddd;font-size:16px}
.newsletter{position:absolute;left:768px;top:128px;width:276px}
.newsletter p{font-size:12px;line-height:16px;color:var(--footer-text)}
.field{width:275px;height:35px;background:var(--field);margin-top:12px;font-size:12px;color:#ddd;padding:10px 20px}
.newsletter .field:first-of-type{margin-top:22px}
.signup{display:inline-block;margin-top:14px;background:linear-gradient(#fff,#e0e0e0);border-radius:3px;font-size:12px;color:#222;padding:10px 20px}
.footer-bar{position:absolute;left:0;top:392px;width:1200px;height:88px;border-top:1px solid #2a2a2a;background:rgba(0,0,0,.08)}
.copyright{position:absolute;left:157px;top:38px;font-size:12px;color:var(--footer-text)}
.footer-social{left:933px;top:30px}
.footer-social span{background:#777}
</style>
</head>
<body>

<header class="site-header">
  <div class="brand"><span class="brand-mark"></span><div>TAVRON<small>Security Services Ltd.</small></div></div>
  <nav class="main-nav"><span>HOME</span><span>ABOUT US</span><span>OUR SECURITY SOLUTIONS</span><span>INDUSTRIES WE SERVE</span><span>CONTACT US</span></nav>
  <div class="social header-social"><span></span><span></span><span></span></div>
</header>

<section class="hero">
  <div class="hero-photo" role="img" aria-label="Security camera mounted on a metal pole"></div>
  <div class="arrow" style="left:103px;top:232px"><svg width="14" height="22"><path d="M11 2 3 11l8 9" fill="none" stroke="#fff" stroke-width="2.5"/></svg></div>
  <div class="arrow" style="left:1046px;top:232px"><svg width="14" height="22"><path d="M3 2l8 9-8 9" fill="none" stroke="#fff" stroke-width="2.5"/></svg></div>
  <h1 class="hero-title"><b>Lorem Ipsum</b> is simply dummy text of<br>the printing and typesetting industry.</h1>
</section>

<section class="solutions">
  <h2 class="section-title" style="top:54px">Our Security Solutions</h2>
  <div class="services-list">
    <h3>Services</h3>
    <ul>
      <li>Property guards</li>
      <li>Corporate events security</li>
      <li>Personal bodyguard for high net worth individuals</li>
      <li>Security consultancy</li>
      <li>Private investigation</li>
    </ul>
  </div>
  <div class="promo">
    <p>CUSTOM OPTIONS<br>AVAILABLE</p>
    <p class="phone">CALL 555-210-482</p>
    <div class="promo-brand"><i></i>TAVRON</div>
  </div>

  <div class="card" style="left:377px;top:151px;width:222px;height:250px">
    <h4><svg width="22" height="22"><path d="M1 11 11 2l10 9h-3v9H4v-9z" fill="#1c1c1c"/></svg>Property Guards</h4>
    <p>Lorem ipsum dolor sit amet, consectetur adipiscing elit, sed diam nonummy nibh euismod tincidunt</p>
    <p>ut laoreet dolore magna aliquam erat volutpat. Ut wisi enim ad minim veniam, quis nostrud exerci tation ullamcorper suscipit lobortis nisl.</p>
    <span class="btn" style="bottom:14px">Read More</span>
  </div>
  <div class="card" style="left:377px;top:401px;width:222px;height:266px">
    <h4><svg width="22" height="22"><circle cx="11" cy="6" r="4.5" fill="#1c1c1c"/><path d="M2 21c0-7 18-7 18 0z" fill="#1c1c1c"/></svg>Corporate Events Security</h4>
    <p>Lorem ipsum dolor sit amet, consectetur adipiscing elit, sed diam nonummy nibh euismod tincidunt ut laoreet dolore magna aliquam erat volutpat. Ut wisi enim ad minim veniam, quis nostrud exerci tation ullamcorper suscipit lobortis nisl ut aliquip ex ea commodo consequat.</p>
    <span class="btn" style="bottom:14px">Read More</span>
  </div>
  <div class="card" style="left:599px;top:151px;width:222px;height:268px">
    <h4><svg width="24" height="22"><circle cx="8" cy="6" r="4.5" fill="#1c1c1c"/><circle cx="16" cy="6" r="4.5" fill="#1c1c1c"/><path d="M0 21c0-8 24-8 24 0z" fill="#1c1c1c"/></svg>Personal Bodyguards</h4>
    <p>Duis autem vel eum iriure dolor in hendrerit in vulputate velit esse molestie consequat.</p>
    <p>Vel illum dolore eu feugiat nulla facilisis at vero eros et accumsan et iusto odio dignissim qui blandit praesent luptatum zzril delenit augue duis dolore te feugait nulla facilisi.</p>
    <span class="btn" style="bottom:14px">Read More</span>
  </div>
  <div class="card" style="left:599px;top:419px;width:222px;height:248px">
    <h4><svg width="24" height="20"><path d="M1 10l6-5 5 3 5-3 6 5-11 8z" fill="#1c1c1c"/></svg>Security Consultancy</h4>
    <p>Duis autem vel eum iriure dolor in hendrerit in vulputate velit esse molestie consequat, vel illum dolore eu feugiat nulla facilisis at vero eros et accumsan et iusto odio dignissim qui blandit praesent luptatum zzril delenit augue duis dolore.</p>
    <span class="btn" style="bottom:14px">Read More</span>
  </div>
  <div class="card" style="left:821px;top:151px;width:222px;height:250px">
    <h4><svg width="22" height="22"><circle cx="9" cy="9" r="6" fill="none" stroke="#1c1c1c" stroke-width="2.5"/><path d="M13 13l8 8" stroke="#1c1c1c" stroke-width="2.5"/></svg>Private Investigation</h4>
    <p>Ut wisi enim ad minim veniam, quis nostrud exerci tation ullamcorper suscipit lobortis nisl ut aliquip ex ea commodo consequat. Duis autem vel eum iriure dolor in hendrerit in vulputate velit.</p>
    <span class="btn" style="bottom:30px">Read More</span>
  </div>
  <div class="card" style="left:821px;top:401px;width:222px;height:266px">
    <h4><svg width="22" height="22"><circle cx="11" cy="9" r="8" fill="none" stroke="#1c1c1c" stroke-width="2.2"/><path d="M6 21h10" stroke="#1c1c1c" stroke-width="2.2"/></svg>Executive Protection</h4>
    <p>Lorem ipsum dolor sit amet, consectetur adipiscing elit, sed diam nonummy nibh euismod tincidunt ut laoreet dolore magna aliquam erat volutpat. Ut wisi enim ad minim veniam, quis nostrud exerci tation ullamcorper suscipit lobortis nisl ut aliquip ex ea commodo consequat.</p>
    <span class="btn" style="bottom:22px">Read More</span>
  </div>
</section>

<section class="industries">
  <h2 class="section-title" style="top:50px">Industries We Serve</h2>
  <div class="arrow small" style="left:107px;top:204px"><svg width="10" height="16"><path d="M8 2 2 8l6 6" fill="none" stroke="#fff" stroke-width="2"/></svg></div>
  <div class="arrow small" style="left:1059px;top:204px"><svg width="10" height="16"><path d="M2 2l6 6-6 6" fill="none" stroke="#fff" stroke-width="2"/></svg></div>
  <div class="industry" style="left:157px"><div class="ph" role="img" aria-label="Guard talking with students on a campus lawn" style="background:linear-gradient(#8fa86a,#4d6a3a)"></div><h5>Campus Security</h5></div>
  <div class="industry" style="left:389px"><div class="ph" role="img" aria-label="Guard on patrol inside a shopping centre" style="background:linear-gradient(#a08a6a,#5a4a3a)"></div><h5>Shoping Center</h5></div>
  <div class="industry" style="left:619px"><div class="ph" role="img" aria-label="Security cameras over an industrial site" style="background:linear-gradient(#dfe8ef,#93a8b8)"></div><h5>Industrial Security</h5></div>
  <div class="industry" style="left:846px"><div class="ph" role="img" aria-label="Officer watching monitors in a control room" style="background:linear-gradient(#4a4a55,#1e1e24)"></div><h5>Security Monitoring</h5></div>
</section>

<section class="split">
  <div class="split-divider"></div>
  <div class="solution" style="left:138px">
    <div class="ph" role="img" aria-label="Resident entering a home alarm code" style="background:linear-gradient(#e2d2bc,#9a7c5c)"></div>
    <h5>Residential Solutions</h5>
    <p>Lorem ipsum dolor sit amet, consectetur adipiscing elit. Sed in porta ut mauris vitae accumsan. Ut bibendum condim Phasellus placerat lectus nec odio fermentum, non Proin nec ligula condimentum, aliquet nisi id,</p>
    <span class="btn">Read More</span>
  </div>
  <div class="solution" style="left:678px">
    <div class="ph" role="img" aria-label="Guard standing before office towers" style="background:linear-gradient(#b8cde0,#34404c)"></div>
    <h5>Commercial Solutions</h5>
    <p>Lorem ipsum dolor sit amet, consectetur adipiscing elit. Sed in porta ut mauris vitae accumsan. Ut bibendum condim Phasellus placerat lectus nec odio fermentum, non Proin nec ligula condimentum, aliquet nisi id,</p>
    <span class="btn">Read More</span>
  </div>
</section>

<footer class="site-footer">
  <h3 style="left:157px">About us</h3>
  <div class="footer-about">
    <p>Lorem ipsum dolor sit amet, consectetur adipiscing elit. Morbi pellentesque iaculis justo eget fermentum. Pellentesque commodo iaculis neque, vitae tincidunt odio pellentesque luctus. Aenean in eros eu magna vestibulum imperdiet pretium nec augue.</p>
    <p>Etiam quis turpis enim. Vestibulum auctor id mauris vulputate consequat. Suspendisse potenti. Cras at imperdiet elit. Integer fringilla tellus non diam condimentum, sed ultricies urna ultricies. Sed cong dui quis dui convallis dictum. Donec malesuada vulputate risus vitae vulputate. Maecenas in congue urna. Sed porttitor bibendum.</p>
  </div>
  <h3 style="left:540px">Quick Links</h3>
  <ul class="quick-links">
    <li>HOME</li><li>OUR SERVICES</li><li>ABOUT</li><li>LOCATIONS</li><li>NEWS</li><li>CAREERS</li><li>CONTACT US</li>
  </ul>
  <h3 style="left:766px">Newsletter Sigup</h3>
  <div class="newsletter">
    <p>Fill the form below and recive our latest offers &amp; updates</p>
    <div class="field">Your Name</div>
    <div class="field">Your Email</div>
    <span class="signup">Signup Now!</span>
  </div>
  <div class="footer-bar">
    <p class="copyright">Copyright © 2014 Tavron Security Service LTD.</p>
    <div class="social footer-social"><span></span><span></span><span></span></div>
  </div>
</footer>

</body>
</html>
```